Specialised investor in e-mobility and energy wants business card design

We need a business card design that fits our existing corporate design. <The look and feel must be 'sharp'/'clean', dynamic, communicate momentum, professionalism etc (as one would imagine from a firm in the financial sector). We like the idea of a reverse-side of the card that includes the logo, and the name and contact details on the other. We expect the deliverable to be whatever format might be required to be able to get cards printed directly by a service such as kelmo press. Our website is www.zub.capital

```html
<!DOCTYPE html>
<html lang="en">
<head>
<meta charset="utf-8">
<title>Zub Capital – Business Card</title>
<link rel="stylesheet" href="https://fonts.googleapis.com/css2?family=Montserrat:wght@400;500;700&display=swap">
<style>
  :root {
    --green-dark: #2f5127;
    --green-light: #86b448;
    --ink: #2a2a2a;
    --paper: #ffffff;
    --backdrop: #e9ebe6;
  }
  * { box-sizing: border-box; margin: 0; padding: 0; }
  html, body { width: 1200px; height: 960px; overflow: hidden; }
  body {
    background: var(--backdrop);
    font-family: "Montserrat", Arial, sans-serif;
    position: relative;
  }
  .card {
    position: absolute;
    left: 250px;
    width: 700px;
    height: 400px;
    background: var(--paper);
    border-radius: 28px;
    overflow: hidden;
    box-shadow: 0 6px 18px rgba(0,0,0,0.12);
  }
  .card--front { top: 36px; }
  .card--back { top: 520px; }

  .wordmark {
    font-weight: 500;
    color: var(--green-dark);
    letter-spacing: 1px;
    white-space: nowrap;
  }
  .card--front .wordmark {
    position: absolute;
    left: 0; right: 0; top: 150px;
    text-align: center;
    font-size: 78px;
    line-height: 1;
  }

  .swoosh { position: absolute; inset: 0; width: 700px; height: 400px; }

  .wordmark--reverse {
    position: absolute;
    right: 54px; top: 36px;
    font-size: 50px;
    color: var(--paper);
    line-height: 1;
  }
  .wordmark--small {
    position: absolute;
    left: 104px; top: 212px;
    font-size: 38px;
    line-height: 1;
  }

  .person { position: absolute; left: 110px; top: 262px; }
  .person__name {
    font-weight: 700;
    font-size: 24px;
    color: var(--green-light);
    letter-spacing: 0.5px;
    line-height: 1.1;
  }
  .person__role { font-size: 17px; color: var(--ink); margin-top: 2px; }

  .contacts { position: absolute; left: 140px; top: 322px; list-style: none; }
  .contacts li {
    display: flex; align-items: center; gap: 8px;
    font-size: 16px; color: var(--ink); line-height: 22px;
  }
  .contacts svg { width: 13px; height: 13px; fill: var(--green-light); flex: none; }

  .company { position: absolute; right: 46px; top: 236px; text-align: right; }
  .company__name { font-size: 17px; color: var(--green-light); font-weight: 500; }
  .company__city { font-size: 17px; color: var(--ink); margin-top: 2px; }
</style>
</head>
<body>

<section class="card card--front" aria-label="Card front">
  <div class="wordmark">zub capital</div>
</section>

<section class="card card--back" aria-label="Card back">
  <svg class="swoosh" viewBox="0 0 700 400" aria-hidden="true">
    <path fill="var(--green-dark)" d="M0,0 H700 V112 C600,168 440,150 300,154 C170,158 80,148 0,150 Z"/>
    <path fill="var(--green-light)" d="M0,150 C80,148 170,158 300,154 C440,150 600,168 700,112 V126 C600,182 440,164 300,168 C170,172 80,162 0,164 Z"/>
    <path fill="var(--green-light)" d="M0,174 C80,166 170,166 270,168 C170,172 80,178 0,186 Z"/>
    <path fill="var(--green-dark)" d="M0,194 C80,182 170,176 270,172 C170,182 80,194 0,210 Z"/>
  </svg>

  <div class="wordmark wordmark--reverse">zub</div>
  <div class="wordmark wordmark--small">zub capital</div>

  <div class="person">
    <div class="person__name">ARON FELDLEY</div>
    <div class="person__role">Managing Director</div>
  </div>

  <ul class="contacts">
    <li>
      <svg viewBox="0 0 16 16"><path d="M3 1l3 3-2 2c1 2 3 4 5 5l2-2 3 3-2 3C6 14 2 10 1 3z"/></svg>
      +41 79 555 0184
    </li>
    <li>
      <svg viewBox="0 0 16 16"><path d="M1 3h14v10H1z M1 3l7 6 7-6" stroke="#fff" stroke-width="1"/></svg>
      aron@zub.capital
    </li>
    <li>
      <svg viewBox="0 0 16 16"><circle cx="8" cy="8" r="7"/><path d="M1 8h14M8 1c3 3 3 11 0 14M8 1c-3 3-3 11 0 14" stroke="#fff" stroke-width="1" fill="none"/></svg>
      www.zub.capital
    </li>
  </ul>

  <div class="company">
    <div class="company__name">Zub Capital S.A.</div>
    <div class="company__city">Geneva, Switzerland</div>
  </div>
</section>

</body>
</html>
```